Professional and creative business card design for recruiting service providers

Our company supports German medium-sized companies in filling vacancies promptly. For this we use social media marketing and bring our customers into the visibility.

We want a professional but also creative design for our business cards.

Please look at lindqvar-staff.de to get an impression of our CI.

Target Market(s)

Small and medium-sized companies in Germany from the industry

Industry/Entity Type

Industrie, Handwerk

Contact Information for Business Card

Name, Position, Telefonnummer, Email, Website

Colors
EE7325
F08F49
F5BC92
FAE3D3
FDF4ED

Requirements
Must have
• A picture of the employee and in the style of www.lindqvar-staff.de

```html
<!DOCTYPE html>
<html lang="de">
<head>
<meta charset="utf-8">
<title>Lindqvar Staff – Visitenkarte</title>
<link href="https://fonts.googleapis.com/css2?family=Montserrat:wght@700&family=Arimo:wght@400;700&display=swap" rel="stylesheet">
<style>
  :root {
    --stage: #2b2623;
    --card-dark: #333333;
    --orange: #ee7325;
    --orange-deep: #e8602a;
    --white: #ffffff;
    --ink: #222222;
    --photo-a: #3a3a3a;
    --photo-b: #1e1e22;
  }
  * { box-sizing: border-box; margin: 0; padding: 0; }
  html, body { width: 1200px; height: 716px; overflow: hidden; }
  body {
    background: var(--stage);
    position: relative;
    font-family: "Arimo", Arial, sans-serif;
  }
  .card {
    position: absolute;
    top: 198px;
    width: 560px;
    height: 320px;
    background: var(--card-dark);
    overflow: hidden;
    box-shadow: 0 10px 30px rgba(0,0,0,.5);
  }
  .card--back { left: 26px; }
  .card--front { left: 614px; }

  .brand {
    display: flex;
    align-items: center;
    gap: 12px;
    font-family: "Montserrat", sans-serif;
    font-weight: 700;
    color: var(--white);
    text-transform: uppercase;
    letter-spacing: 3px;
    line-height: 1.05;
  }
  .brand__mark {
    width: 18px; height: 18px;
    background: var(--orange);
    flex: none;
  }
  .card--back .brand {
    position: absolute;
    left: 50%; top: 50%;
    transform: translate(-50%, -50%);
    font-size: 30px;
  }
  .card--back .brand__mark { width: 26px; height: 26px; }

  .portrait {
    position: absolute;
    left: 0; top: 0;
    width: 270px; height: 320px;
    background: linear-gradient(160deg, var(--photo-a), var(--photo-b));
  }
  .bands { position: absolute; inset: 0; }

  .card--front .brand {
    position: absolute;
    right: 26px; top: 42px;
    font-size: 22px;
  }
  .person {
    position: absolute;
    right: 26px; top: 112px;
    text-align: right;
  }
  .person__name {
    color: var(--orange);
    font-size: 18px;
    font-weight: 700;
    text-transform: uppercase;
    letter-spacing: .5px;
  }
  .person__role {
    color: var(--white);
    font-size: 15px;
    margin-top: 2px;
  }
  .contact {
    position: absolute;
    right: 22px; top: 196px;
    list-style: none;
    text-align: right;
    color: var(--ink);
    font-size: 13px;
    line-height: 20px;
  }
  .contact li { display: flex; justify-content: flex-end; align-items: center; gap: 8px; }
  .contact svg { width: 13px; height: 13px; flex: none; }
  .address {
    position: absolute;
    right: 26px; top: 272px;
    text-align: right;
    color: var(--white);
    font-size: 13px;
    line-height: 18px;
    font-style: normal;
  }
</style>
</head>
<body>
  <section class="card card--back" aria-label="Kartenrückseite">
    <div class="brand"><span class="brand__mark"></span><span>Lindqvar<br>Staff</span></div>
  </section>

  <section class="card card--front" aria-label="Kartenvorderseite">
    <div class="portrait" role="img" aria-label="Porträtfoto des Mitarbeiters in dunklem Sakko vor dunklem Hintergrund"></div>
    <svg class="bands" viewBox="0 0 560 320" aria-hidden="true">
      <polygon points="250,178 560,200 560,266 270,266" fill="var(--white)"/>
      <polygon points="270,266 560,266 560,320 266,320" fill="var(--orange-deep)"/>
    </svg>

    <div class="brand"><span class="brand__mark"></span><span>Lindqvar<br>Staff</span></div>

    <div class="person">
      <p class="person__name">Tobias Brenner</p>
      <p class="person__role">Manager</p>
    </div>

    <ul class="contact">
      <li>0172 430 9157
        <svg viewBox="0 0 24 24"><path d="M6.6 10.8a15 15 0 0 0 6.6 6.6l2.2-2.2c.3-.3.7-.4 1-.2 1.1.4 2.3.6 3.6.6.6 0 1 .4 1 1V20c0 .6-.4 1-1 1A17 17 0 0 1 3 4c0-.6.4-1 1-1h3.5c.6 0 1 .4 1 1 0 1.3.2 2.5.6 3.6.1.3 0 .7-.2 1z" fill="var(--orange)"/></svg>
      </li>
      <li>info@lindqvar-staff.de
        <svg viewBox="0 0 24 24"><rect x="3" y="5" width="18" height="14" rx="1" fill="none" stroke="var(--orange)" stroke-width="2"/><path d="M3 6l9 7 9-7" fill="none" stroke="var(--orange)" stroke-width="2"/></svg>
      </li>
      <li>www.lindqvar-staff.de
        <svg viewBox="0 0 24 24"><circle cx="12" cy="12" r="9" fill="none" stroke="var(--orange)" stroke-width="2"/><path d="M3 12h18M12 3c3 3 3 15 0 18M12 3c-3 3-3 15 0 18" fill="none" stroke="var(--orange)" stroke-width="1.6"/></svg>
      </li>
    </ul>

    <address class="address">Kastanienallee 52<br>70174 Stuttgart</address>
  </section>
</body>
</html>
```